VocaTerrana Community/ Talent Gallery

VocaTerrana is developing a collaborative career course, with coaching and community exchange. Goal is to offer a platform where talented candidates can show their expertise and find projects, partners, and develop their online portfolios!

Here is a good example of the type of thing we hope to create with focus on sustainability focused talent to task matching
http://www.brambleforth.com/global-themes/employment-and-growth/connecting-talent-with-opportunity-in-the-digital-age

We hope to have a "grid style" gallery where it is easy to search by talent types and focus areas within the scope of "Sustainability" issues...Food/Water/Energy, Public Health, Technology, Sustainable Cities, Infrastructure, Education, Policy, Emerging Economies, Ecosystems, Social Innovation, inclusive Security, Equity Issues. For each topic/ header we hope to have candidates post their completed portfolios to exhibit resumes, biography, a case study... they may actually prepare these on other sites, but can link in OR alternately that they can easily create here, similar to "pinqo.io" ....

Hope to include a blog space titled "Rising over the Rift", where people can mix it up across these topic issues as they are interdependent and often require partners across discipline areas! If possible another area where jobs related to these issues may be posted as project or job opportunities by potential employers.

If there is a way to create a feed from various job sites that already exist...like Jobora...or http://www.greenledgerworks.com/ that would be super great. Again...sort of a portal connection to bridge the gap ....instead of candidates having to search all the time, we are hoping they can advertise their talent and employers may search here for these well presented portfolios!

Target Market(s)

Educators, Students, Career Transitioners, Employers, Professional Associations, Talent Recruiters with focus on Sustainability related Talent to Task matching!

Industry/Entity Type

Sustainability

Number of Pages Required

4 page

Font styles to use
Sans Serif

Colors
3176b5
32b8a4
add136

Requirements
Must have
• Not sure about the coded/ uncoded option here....
• Must have - grid style area where Sustainability Professionals with varied focus areas can exhibit their talent portfolios
• appear as a Talent Gallery that starts with photos & obvious organization...other tabs to be in a menu.
• ability to search both talent and task opportunity areas to help coaches or community members make matches....some topic focused category or tag words to help make them searchable...???
• consistent professional styling to existing website and new artflock postcard shared in brief/ images area
• Interactive blog space where articles, issues may be posted, discussed
• Bulletin board or feed for project opportunities to be posted where candidates may locate them and/or employers may express specific "call" for talent..These may be Short term Internships, Projects, Consulting Team Opportunity, or Jobs/ part time to full time....
Nice to have
• A calendar area where we can post networking opportunities, issues presentations where potential partners can meet the next generation leaders, attend a forum or webinar presentation.
Should not have
• Too much text on front page...Should be clean design,

```html
<!DOCTYPE html>
<html lang="en">
<head>
<meta charset="utf-8">
<title>VocaTerrana — Career Collaboration for a Sustainable Future</title>
<link href="https://fonts.googleapis.com/css2?family=Open+Sans:wght@400;600;700;800&display=swap" rel="stylesheet">
<style>
:root{
  --blue:#3176b5;
  --blue-dark:#2a5fa6;
  --teal:#32b8a4;
  --green:#add136;
  --green-deep:#8cbf2f;
  --ink:#1f1f1f;
  --text:#555b61;
  --muted:#777;
  --panel:#e9edf2;
  --card:#f2f3f4;
  --cell:#d7d9dc;
  --footer:#161616;
  --white:#fff;
}
*{box-sizing:border-box;margin:0;padding:0}
html,body{width:1200px;height:2839px;overflow:hidden}
body{font-family:"Open Sans",Arial,sans-serif;color:var(--text);background:var(--white);position:relative}
a{text-decoration:none;color:inherit}
.abs{position:absolute}
section,header,footer{position:absolute;left:0;width:1200px}

/* header */
.site-header{top:0;height:85px;background:var(--white);border-top:4px solid transparent;
  border-image:linear-gradient(90deg,var(--green),var(--teal),var(--blue)) 1}
.brand{left:100px;top:14px;display:flex;align-items:center;gap:12px}
.brand-dot{width:50px;height:50px;border-radius:50%;background:var(--teal)}
.brand-name{font-weight:700;font-size:21px;color:var(--ink)}
.main-nav{top:30px;font-size:14px;font-weight:600;color:var(--ink)}
.main-nav a{position:absolute;white-space:nowrap}
.main-nav .active{color:var(--green-deep)}
.nav-search{left:972px;top:30px}
.login-btn{left:1020px;top:21px;width:80px;height:37px;background:var(--green-deep);border-radius:3px;color:#fff;
  font-size:13px;font-weight:700;display:flex;align-items:center;justify-content:center;gap:4px;box-shadow:0 2px 0 #6f9b1f}

/* hero */
.hero{top:85px;height:422px;background:linear-gradient(180deg,#3b3530 0%,#5a4b3e 45%,#4a3f35 70%,#2f2a25 100%)}
.hero-photo{position:absolute;inset:0;background:radial-gradient(ellipse 380px 240px at 600px 280px,rgba(120,140,70,.45),transparent 70%),radial-gradient(ellipse 700px 300px at 600px 380px,rgba(150,115,90,.45),transparent 70%)}
.hero-title{left:0;width:1200px;top:98px;text-align:center;color:#fff;font-weight:700;font-size:40px;text-shadow:0 2px 6px rgba(0,0,0,.4)}
.hero-sub{left:0;width:1200px;top:150px;text-align:center;color:#fff;font-size:24px;font-weight:600;word-spacing:4px}
.hero-sub span{margin:0 14px;font-weight:400}
.search-box{left:214px;top:214px;width:770px;height:104px;border:2px solid rgba(255,255,255,.85)}
.search-box label{position:absolute;top:17px;color:#fff;font-size:14px;font-weight:700}
.search-box .field{position:absolute;top:41px;height:40px;background:#fff;border-radius:2px}
.search-btn{position:absolute;left:630px;top:26px;width:122px;height:56px;background:var(--green-deep);border-radius:3px;
  color:#fff;font-weight:700;font-size:16px;display:flex;align-items:center;justify-content:center;gap:8px;box-shadow:0 3px 0 #6f9b1f}
.slide-arrow{width:34px;height:34px;border-radius:50%;background:rgba(0,0,0,.35);display:flex;align-items:center;justify-content:center}

/* headings */
.section-title{left:0;width:1200px;text-align:center;color:var(--ink);font-weight:700;font-size:23px}
.section-lead{left:160px;width:880px;text-align:center;font-size:14.5px;line-height:26px;color:var(--text)}

/* welcome */
.welcome{top:507px;height:549px}
.pillar{top:237px;width:307px;height:255px;background:var(--card)}
.pillar-icon{position:absolute;left:93px;top:-60px;width:120px;height:120px;border-radius:50%;display:flex;align-items:center;justify-content:center}
.pillar h3{position:absolute;top:82px;width:100%;text-align:center;color:var(--ink);font-size:17px;font-weight:700}
.pillar p{position:absolute;top:122px;left:0;right:0;text-align:center;font-size:11px;line-height:24px;white-space:nowrap}
.pillar .more{position:absolute;top:210px;width:100%;text-align:center;font-size:12px;font-weight:700}
.pillar.course{border-bottom:3px solid var(--blue-dark)}
.pillar.coaching{border-bottom:3px solid var(--teal)}
.pillar.community{border-bottom:3px solid var(--green)}

/* rift */
.rift{top:1056px;height:538px;background:var(--panel)}
.post{top:108px;width:320px}
.post-photo{width:320px;height:205px}
.post h3{margin-top:20px;font-size:17px;font-weight:700;color:var(--ink)}
.post .meta{margin-top:6px;font-size:12px;color:var(--blue-dark);display:flex;align-items:center;gap:8px}
.post p{margin-top:12px;font-size:11.5px;line-height:22px;color:var(--text)}
.post .more{display:block;margin-top:12px;font-size:12.5px;font-weight:700;color:var(--green-deep)}
.side-arrow{top:200px}

/* phases */
.phases{top:1594px;height:424px}
.phase{top:177px;width:152px;height:152px;border:4px solid var(--blue-dark);border-radius:50%;background:#fff;display:flex;align-items:center;justify-content:center}
.phase-num{position:absolute;right:-12px;top:20px;width:38px;height:38px;border-radius:50%;background:var(--blue-dark);color:#fff;
  font-weight:700;font-size:17px;display:flex;align-items:center;justify-content:center;border:3px solid #fff}
.phase-label{top:348px;width:200px;text-align:center;color:var(--ink);font-weight:700;font-size:17px}
.phase-link{top:252px;height:2px;background:#c9ccd0}

/* calendar + news */
.agenda{top:2018px;height:496px;background:var(--panel)}
.calendar{left:100px;top:49px;width:411px;height:386px;background:#fff;border:1px solid #dfe2e6}
.cal-head{position:absolute;left:26px;top:8px;width:358px;height:47px;background:var(--blue-dark);color:#fff;display:flex;align-items:center;justify-content:space-between;padding:0 18px;font-weight:700;font-size:21px}
.cal-days,.cal-grid{position:absolute;left:25px;display:grid;grid-template-columns:repeat(7,44px);column-gap:9.5px}
.cal-days{top:70px;font-weight:700;font-size:18px;color:var(--ink);text-align:center}
.cal-grid{top:118px;row-gap:8px}
.cal-grid span{height:44px;background:var(--cell);display:flex;align-items:center;justify-content:center;font-size:18px;color:var(--ink)}
.cal-grid .blank{background:none}
.cal-grid .today{background:var(--green-deep);color:#fff;font-weight:700}
.news-title{left:568px;top:52px;font-size:23px;font-weight:700;color:var(--ink)}
.news-item{left:568px;width:532px;height:153px}
.news-photo{position:absolute;left:6px;top:0;width:119px;height:110px;border:3px solid #fff;box-shadow:0 0 0 1px #dde}
.news-item h4{position:absolute;left:153px;top:0;font-size:15.5px;font-weight:700;color:var(--ink);white-space:nowrap}
.news-item .date{position:absolute;left:153px;top:27px;font-size:13px;color:var(--blue-dark);display:flex;gap:8px;align-items:center}
.news-item p{position:absolute;left:153px;top:55px;width:375px;font-size:12.5px;line-height:23px}
.news-rule{left:568px;width:532px;height:1px;background:#cfd3d8}
.view-more{left:568px;top:2427px;font-size:12.5px;font-weight:700;color:var(--green-deep)}

/* footer */
.site-footer{top:2514px;height:325px;background:var(--footer);color:#ddd;border-top:5px solid transparent;
  border-image:linear-gradient(90deg,var(--green),var(--teal),var(--blue)) 1}
.foot-brand{left:100px;top:100px;display:flex;align-items:center;gap:14px;color:#fff;font-weight:700;font-size:24px}
.foot-brand i{width:56px;height:56px;border-radius:50%;background:var(--teal);display:block}
.foot-col h5{font-size:14.5px;font-weight:700;color:#fff;margin-bottom:20px}
.foot-col li{list-style:none;font-size:12.5px;line-height:29.4px}
.foot-col p{font-size:12.5px;line-height:22px}
.email-field{width:261px;height:33px;background:#fff;color:#444;font-size:12px;padding:9px 14px;margin-top:22px}
.subscribe{margin-top:21px;width:99px;height:36px;border:2px solid #fff;border-radius:3px;color:#fff;font-weight:700;font-size:12.5px;display:flex;align-items:center;justify-content:center}
.contact-row{display:flex;gap:18px;font-size:12.5px;line-height:24px}
.copyright{left:100px;top:280px;font-size:12px;color:#ccc}
.social{top:268px;width:34px;height:34px;border:2px solid #fff;border-radius:50%}
</style>
</head>
<body>

<header class="site-header">
  <a class="brand abs" href="#"><span class="brand-dot"></span><span class="brand-name">VocaTerrana</span></a>
  <nav class="main-nav abs" style="left:0">
    <a class="active" style="left:488px">HOME</a>
    <a style="left:574px">ABOUT</a>
    <a style="left:667px">SERVICES</a>
    <a style="left:777px">BLOG</a>
    <a style="left:860px">CONTACT</a>
  </nav>
  <svg class="nav-search abs" width="16" height="16" viewBox="0 0 16 16" aria-label="Search"><circle cx="6.5" cy="6.5" r="5" fill="none" stroke="#222" stroke-width="2"/><line x1="10" y1="10" x2="14.5" y2="14.5" stroke="#222" stroke-width="2.4"/></svg>
  <a class="login-btn abs" href="#"><svg width="10" height="12" viewBox="0 0 10 12"><rect x="1" y="5" width="8" height="7" fill="#fff"/><path d="M3 5V3.5a2 2 0 0 1 4 0V5" fill="none" stroke="#fff" stroke-width="1.5"/></svg>LOGIN</a>
</header>

<section class="hero">
  <div class="hero-photo" role="img" aria-label="Cupped hands holding soil with a young green seedling"></div>
  <h1 class="hero-title abs">Career Collaboration for a Sustainable Future</h1>
  <p class="hero-sub abs">Course<span>|</span>Coaching<span>|</span>Community</p>
  <form class="search-box abs">
    <label style="left:18px">Talent</label>
    <div class="field" style="left:18px;width:288px"></div>
    <label style="left:318px">Task Opportunity Areas</label>
    <div class="field" style="left:318px;width:288px"></div>
    <div class="search-btn"><svg width="15" height="15" viewBox="0 0 16 16"><circle cx="6.5" cy="6.5" r="5" fill="none" stroke="#fff" stroke-width="2.4"/><line x1="10" y1="10" x2="14.5" y2="14.5" stroke="#fff" stroke-width="2.8"/></svg>SEARCH</div>
  </form>
  <div class="slide-arrow abs" style="left:30px;top:193px"><svg width="10" height="14" viewBox="0 0 10 14"><path d="M8 1 2 7l6 6" fill="none" stroke="#fff" stroke-width="2"/></svg></div>
  <div class="slide-arrow abs" style="left:1134px;top:193px"><svg width="10" height="14" viewBox="0 0 10 14"><path d="M2 1l6 6-6 6" fill="none" stroke="#fff" stroke-width="2"/></svg></div>
</section>

<section class="welcome">
  <h2 class="section-title abs" style="top:46px">WELCOME TO VOCATERRANA</h2>
  <p class="section-lead abs" style="top:94px">Our mission is to cultivate a community of learning and professional practice to support career transitions and next generation leadership of sustainable solutions that balance economic, environment, and equity as we meet local-to-global change.</p>

  <article class="pillar course abs" style="left:98px">
    <div class="pillar-icon" style="background:var(--blue-dark)">
      <svg width="64" height="52" viewBox="0 0 64 52"><path d="M32 4 2 18l30 14 30-14z" fill="#fff"/><path d="M14 25v12c0 6 36 6 36 0V25L32 33z" fill="#fff"/><line x1="56" y1="20" x2="56" y2="40" stroke="#fff" stroke-width="2.5"/><circle cx="56" cy="42" r="3" fill="#fff"/></svg>
    </div>
    <h3>COURSE</h3>
    <p>Individual inquiry and creative talent development<br>are facilitated by professional coaches, activated<br>through experiential learning projects</p>
    <a class="more" style="color:var(--blue-dark)">READ MORE &gt;&gt;</a>
  </article>
  <article class="pillar coaching abs" style="left:447px">
    <div class="pillar-icon" style="background:var(--teal)">
      <svg width="60" height="58" viewBox="0 0 60 58"><rect x="6" y="6" width="48" height="34" fill="none" stroke="#fff" stroke-width="3"/><rect x="16" y="24" width="6" height="12" fill="#fff"/><rect x="27" y="16" width="6" height="20" fill="#fff"/><rect x="38" y="12" width="6" height="24" fill="#fff"/><line x1="30" y1="40" x2="18" y2="56" stroke="#fff" stroke-width="3"/><line x1="30" y1="40" x2="42" y2="56" stroke="#fff" stroke-width="3"/><rect x="2" y="2" width="56" height="5" fill="#fff"/></svg>
    </div>
    <h3>COACHING</h3>
    <p>Individual inquiry and creative talent development<br>are facilitated by professional coaches, activated<br>through experiential learning projects</p>
    <a class="more" style="color:var(--teal)">READ MORE &gt;&gt;</a>
  </article>
  <article class="pillar community abs" style="left:793px">
    <div class="pillar-icon" style="background:var(--green)">
      <svg width="64" height="60" viewBox="0 0 64 60"><g stroke="#fff" stroke-width="2.5" fill="none"><line x1="10" y1="12" x2="32" y2="4"/><line x1="32" y1="4" x2="54" y2="12"/><line x1="10" y1="12" x2="6" y2="34"/><line x1="54" y1="12" x2="58" y2="34"/><line x1="10" y1="12" x2="32" y2="22"/><line x1="54" y1="12" x2="32" y2="22"/></g><g fill="#fff"><circle cx="10" cy="12" r="5"/><circle cx="32" cy="4" r="4"/><circle cx="54" cy="12" r="5"/><circle cx="6" cy="34" r="4"/><circle cx="58" cy="34" r="4"/><circle cx="32" cy="26" r="6"/><path d="M20 58c0-14 24-14 24 0z"/></g></svg>
    </div>
    <h3>COMMUNITY</h3>
    <p>Individual inquiry and creative talent development<br>are facilitated by professional coaches, activated<br>through experiential learning projects</p>
    <a class="more" style="color:var(--green-deep)">READ MORE &gt;&gt;</a>
  </article>
</section>

<section class="rift">
  <h2 class="section-title abs" style="top:45px">RISING OVER THE RIFT</h2>
  <svg class="abs side-arrow" style="left:50px" width="14" height="22" viewBox="0 0 14 22"><path d="M12 1 2 11l10 10" fill="none" stroke="#9aa0a6" stroke-width="2"/></svg>
  <svg class="abs side-arrow" style="left:1134px" width="14" height="22" viewBox="0 0 14 22"><path d="M2 1l10 10-10 10" fill="none" stroke="#9aa0a6" stroke-width="2"/></svg>

  <article class="post abs" style="left:98px">
    <div class="post-photo" role="img" aria-label="Water rushing from the gates of a hydroelectric dam" style="background:linear-gradient(180deg,#8a9aa8 0%,#6e7f8c 40%,#c9d3da 70%,#5c6b63 100%)"></div>
    <h3>FOOD/WATER/ENERGY</h3>
    <div class="meta"><svg width="12" height="12" viewBox="0 0 12 12"><rect x="1" y="2" width="10" height="9" fill="var(--blue-dark)"/><rect x="2" y="5" width="8" height="5" fill="#fff"/></svg>February 1, 2016 <span>|</span><svg width="11" height="12" viewBox="0 0 11 12"><circle cx="5.5" cy="3.5" r="3" fill="var(--blue-dark)"/><path d="M0 12c0-6 11-6 11 0z" fill="var(--blue-dark)"/></svg>Marisol Ventrekka</div>
    <p>Everybody Eats! Maybe we do not eat all the same types of things, depending on whether you are a human being, animal or plant, but every organic ..</p>
    <a class="more">READ MORE &gt;&gt;</a>
  </article>
  <article class="post abs" style="left:439px">
    <div class="post-photo" role="img" aria-label="Runner drinking from a water bottle outdoors in warm light" style="background:linear-gradient(135deg,#3d4a1f 0%,#7a6a2a 40%,#c98a4a 65%,#5a4a22 100%)"></div>
    <h3>PUBLIC HEALTH</h3>
    <div class="meta"><svg width="12" height="12" viewBox="0 0 12 12"><rect x="1" y="2" width="10" height="9" fill="var(--blue-dark)"/><rect x="2" y="5" width="8" height="5" fill="#fff"/></svg>February 1, 2016 <span>|</span><svg width="11" height="12" viewBox="0 0 11 12"><circle cx="5.5" cy="3.5" r="3" fill="var(--blue-dark)"/><path d="M0 12c0-6 11-6 11 0z" fill="var(--blue-dark)"/></svg>Marisol Ventrekka</div>
    <p>Everybody Eats! Maybe we do not eat all the same types of things, depending on whether you are a human being, animal or plant, but every organic ..</p>
    <a class="more">READ MORE &gt;&gt;</a>
  </article>
  <article class="post abs" style="left:780px">
    <div class="post-photo" role="img" aria-label="Hands typing on a laptop with a digital overlay" style="background:linear-gradient(135deg,#e8ecef 0%,#b9c3cb 45%,#8b97a1 75%,#d5dbe0 100%)"></div>
    <h3>TECHNOLOGY</h3>
    <div class="meta"><svg width="12" height="12" viewBox="0 0 12 12"><rect x="1" y="2" width="10" height="9" fill="var(--blue-dark)"/><rect x="2" y="5" width="8" height="5" fill="#fff"/></svg>February 1, 2016 <span>|</span><svg width="11" height="12" viewBox="0 0 11 12"><circle cx="5.5" cy="3.5" r="3" fill="var(--blue-dark)"/><path d="M0 12c0-6 11-6 11 0z" fill="var(--blue-dark)"/></svg>Marisol Ventrekka</div>
    <p>Everybody Eats! Maybe we do not eat all the same types of things, depending on whether you are a human being, animal or plant, but every organic ..</p>
    <a class="more">READ MORE &gt;&gt;</a>
  </article>
</section>

<section class="phases">
  <h2 class="section-title abs" style="top:46px">FOUR PHASE CAREER COURSE</h2>
  <p class="section-lead abs" style="top:91px;left:150px;width:900px">Through a proven four-phase process, integrating principles of lifelong learning, career transitions, entrepreneurship, change management, and innovation, our interdisciplinary, collaborative course is designed to guide</p>

  <div class="phase-link abs" style="left:254px;width:134px"></div>
  <svg class="abs" style="left:308px;top:244px" width="14" height="18" viewBox="0 0 14 18"><path d="M2 1l9 8-9 8" fill="none" stroke="#c9ccd0" stroke-width="3"/></svg>
  <div class="phase-link abs" style="left:542px;width:120px"></div>
  <svg class="abs" style="left:594px;top:244px" width="14" height="18" viewBox="0 0 14 18"><path d="M2 1l9 8-9 8" fill="none" stroke="#c9ccd0" stroke-width="3"/></svg>
  <div class="phase-link abs" style="left:818px;width:126px"></div>
  <svg class="abs" style="left:874px;top:244px" width="14" height="18" viewBox="0 0 14 18"><path d="M2 1l9 8-9 8" fill="none" stroke="#c9ccd0" stroke-width="3"/></svg>

  <div class="phase abs" style="left:100px">
    <svg width="70" height="74" viewBox="0 0 70 74"><path d="M8 4h32l12 12v32H8z" fill="var(--green-deep)"/><g stroke="#fff" stroke-width="3"><line x1="16" y1="22" x2="40" y2="22"/><line x1="16" y1="31" x2="40" y2="31"/><line x1="16" y1="40" x2="30" y2="40"/></g><circle cx="46" cy="52" r="11" fill="#fff" stroke="var(--green-deep)" stroke-width="4"/><line x1="54" y1="60" x2="64" y2="70" stroke="var(--green-deep)" stroke-width="6"/></svg>
    <span class="phase-num">1</span>
  </div>
  <div class="phase abs" style="left:388px">
    <svg width="78" height="64" viewBox="0 0 78 64"><path d="M39 4C18 4 4 16 4 30c0 8 5 15 12 19l-4 13 16-9c3 1 7 1 11 1 21 0 35-12 35-24S60 4 39 4z" fill="var(--green-deep)"/><circle cx="24" cy="30" r="5" fill="#fff"/><circle cx="39" cy="30" r="5" fill="#fff"/><circle cx="54" cy="30" r="5" fill="#fff"/></svg>
    <span class="phase-num">2</span>
  </div>
  <div class="phase abs" style="left:664px">
    <svg width="76" height="76" viewBox="0 0 76 76"><g fill="var(--green-deep)"><rect x="6" y="6" width="26" height="26"/><rect x="44" y="6" width="26" height="26"/><rect x="6" y="44" width="26" height="26"/><rect x="44" y="44" width="26" height="26"/><circle cx="38" cy="19" r="7"/><circle cx="19" cy="38" r="7"/><circle cx="57" cy="38" r="7"/><circle cx="38" cy="57" r="7"/></g></svg>
    <span class="phase-num">3</span>
  </div>
  <div class="phase abs" style="left:946px">
    <svg width="72" height="72" viewBox="0 0 72 72"><path d="M44 10H10v52h52V28" fill="none" stroke="var(--green-deep)" stroke-width="6"/><path d="M56 4l12 12-30 30-16 4 4-16z" fill="var(--green-deep)"/><path d="M26 38l8 8" stroke="#fff" stroke-width="2"/></svg>
    <span class="phase-num">4</span>
  </div>

  <p class="phase-label abs" style="left:76px">CLARIFY</p>
  <p class="phase-label abs" style="left:364px">COMMUNICATE</p>
  <p class="phase-label abs" style="left:640px">COLLABORATE</p>
  <p class="phase-label abs" style="left:922px">CREATE</p>
</section>

<section class="agenda">
  <div class="calendar abs">
    <div class="cal-head">
      <svg width="12" height="16" viewBox="0 0 12 16"><path d="M11 1 1 8l10 7z" fill="#fff"/></svg>
      <span>February 2016</span>
      <svg width="12" height="16" viewBox="0 0 12 16"><path d="M1 1l10 7-10 7z" fill="#fff"/></svg>
    </div>
    <div class="cal-days"><span>Su</span><span>Mo</span><span>Tu</span><span>We</span><span>Th</span><span>Fr</span><span>Sa</span></div>
    <div class="cal-grid">
      <span class="blank"></span><span class="blank"></span><span class="blank"></span><span>1</span><span>2</span><span>3</span><span>4</span>
      <span>5</span><span>6</span><span>7</span><span>8</span><span>9</span><span>10</span><span>11</span>
      <span>12</span><span>13</span><span>14</span><span class="today">15</span><span>16</span><span>17</span><span>18</span>
      <span>19</span><span>20</span><span>21</span><span>22</span><span>23</span><span>24</span><span>25</span>
      <span>26</span><span>27</span><span>28</span><span>29</span><span>30</span><span>31</span><span class="blank"></span>
    </div>
  </div>

  <h2 class="news-title abs">NEWS AND EVENTS</h2>
  <article class="news-item abs" style="top:115px">
    <div class="news-photo" role="img" aria-label="Group of people seated together on grass at an outdoor gathering" style="background:linear-gradient(180deg,#7f9a5a 0%,#5f7a3e 55%,#8a7a5a 100%)"></div>
    <h4>AT VERO EOS ET ACCUSAMUS ET IUSTO ODIO DIG</h4>
    <div class="date"><svg width="12" height="12" viewBox="0 0 12 12"><rect x="1" y="2" width="10" height="9" fill="var(--blue-dark)"/><rect x="2" y="5" width="8" height="5" fill="#fff"/></svg>05/03/2016</div>
    <p>Nemo enim ipsam voluptatem quia voluptas sit aspernatur aut odit aut fugit, sed quia consequuntur..</p>
  </article>
  <div class="news-rule abs" style="top:246px"></div>
  <article class="news-item abs" style="top:268px">
    <div class="news-photo" role="img" aria-label="People in business attire meeting around a conference table" style="background:linear-gradient(180deg,#c8c2b8 0%,#6d6660 50%,#3a3532 100%)"></div>
    <h4>AT VERO EOS ET ACCUSAMUS ET IUSTO ODIO DIG</h4>
    <div class="date"><svg width="12" height="12" viewBox="0 0 12 12"><rect x="1" y="2" width="10" height="9" fill="var(--blue-dark)"/><rect x="2" y="5" width="8" height="5" fill="#fff"/></svg>05/03/2016</div>
    <p>Nemo enim ipsam voluptatem quia voluptas sit aspernatur aut odit aut fugit, sed quia consequuntur..</p>
  </article>
  <div class="news-rule abs" style="top:399px"></div>
</section>
<a class="view-more abs" href="#">VIEW MORE &gt;&gt;</a>

<footer class="site-footer">
  <div class="foot-brand abs"><i></i>VocaTerrana</div>

  <div class="foot-col abs" style="left:394px;top:34px">
    <h5>INFORMATION</h5>
    <ul><li>Home</li><li>About</li><li>Services</li><li>Blog</li><li>Contact</li></ul>
  </div>

  <div class="foot-col abs" style="left:581px;top:34px">
    <h5>NEWSLETTER</h5>
    <p>Register your email address to get<br>information ablout us</p>
    <div class="email-field">Email Address</div>
    <div class="subscribe">SUBSCRIBE</div>
  </div>

  <div class="foot-col abs" style="left:910px;top:34px">
    <h5>CONTACT US</h5>
    <div class="contact-row"><svg width="10" height="16" viewBox="0 0 10 16" style="margin-top:4px"><path d="M5 0a5 5 0 0 0-5 5c0 4 5 11 5 11s5-7 5-11a5 5 0 0 0-5-5z" fill="#fff"/><circle cx="5" cy="5" r="2" fill="var(--footer)"/></svg><span>1290 Meadowline Ave, Suite 210,<br>OH 4000 Fernwick</span></div>
    <div class="contact-row" style="margin-top:22px"><svg width="12" height="12" viewBox="0 0 12 12" style="margin-top:6px"><path d="M2 0h3l1 3-2 1.5a7 7 0 0 0 3.5 3.5L9 6l3 1v3a2 2 0 0 1-2 2A10 10 0 0 1 0 2a2 2 0 0 1 2-2z" fill="#fff"/></svg><span>1 555 010 200</span></div>
    <div class="contact-row" style="margin-top:22px"><svg width="13" height="10" viewBox="0 0 13 10" style="margin-top:7px"><rect width="13" height="10" fill="#fff"/><path d="M0 0l6.5 5L13 0" fill="none" stroke="var(--footer)" stroke-width="1.2"/></svg><span>info@vocaterrana.com</span></div>
  </div>

  <p class="copyright abs">Copyrights © 2016, VocaTerrana . All rights reserved.</p>
  <a class="social abs" style="left:950px" aria-label="Social profile 1"></a>
  <a class="social abs" style="left:989px" aria-label="Social profile 2"></a>
  <a class="social abs" style="left:1028px" aria-label="Social profile 3"></a>
  <a class="social abs" style="left:1067px" aria-label="Social profile 4"></a>
</footer>

</body>
</html>
```